Letterhead and matching envelope design for a dental office

We need a new stationary design, letterhead and envelope #10, for a dental office in Denver area. We are called Bright Harbor Dental. We want a simple and minimalistic design but not a boring design. I wish to have one good point that makes it look professional. I have attached our logo. Feel free to use either one. I want the design for letterhead and envelope look like a "matching pair" but not look the same. The envelope doesn't have to be white and it will have an address window on bottom left.

Target Market(s)

everyone who visits dentist (adults)

Industry/Entity Type

Dental

Font styles to use
Other font styles liked:
• close to font on logo or something that matches well

Requirements
Must have
• professional
• simple, minimalistic
• unique point that stands out
Nice to have
• matching but not same design for letterhead and envelope
Should not have
• not look like all the other boring designs
• no flowery, distracting feats

```html
<!DOCTYPE html>
<html lang="en">
<head>
<meta charset="utf-8">
<title>Bright Harbor Dental – Stationery</title>
<link href="https://fonts.googleapis.com/css2?family=Source+Sans+3:wght@400;600;700&display=swap" rel="stylesheet">
<style>
  :root {
    --green: #3bb54a;
    --green-soft: #a9dba9;
    --green-pale: #e4f1e1;
    --ink: #3a3a3a;
    --paper: #ffffff;
    --backdrop: #ebebeb;
  }
  * { box-sizing: border-box; margin: 0; padding: 0; }
  html, body { width: 1200px; height: 799px; overflow: hidden; }
  body {
    background: var(--backdrop);
    font-family: "Source Sans 3", "Myriad Pro", Arial, sans-serif;
    color: var(--ink);
    position: relative;
  }
  .sheet {
    position: absolute;
    background: var(--paper);
    overflow: hidden;
    box-shadow: 0 6px 18px rgba(0,0,0,.12);
  }
  .brand {
    display: flex; align-items: center; gap: 8px;
    color: var(--green); font-weight: 600; letter-spacing: .04em;
  }
  .brand-dot { width: 14px; height: 14px; border-radius: 50%; background: var(--green); }
  .address { font-size: 10.5px; line-height: 1.35; }
  .address .name { color: var(--green); }
  .contacts { list-style: none; font-size: 10.5px; line-height: 1.55; }
  .contacts li { display: flex; align-items: center; gap: 5px; }
  .contacts svg { width: 10px; height: 10px; flex: none; }
  .wave { position: absolute; left: 0; bottom: 0; width: 100%; }
  .leaf-art {
    position: absolute; border-radius: 50%;
    background: radial-gradient(ellipse at center, var(--green-pale) 0%, rgba(228,241,225,0) 70%);
  }

  /* Letterhead */
  .letterhead { left: 80px; top: 95px; width: 470px; height: 608px; }
  .letterhead .brand { position: absolute; top: 34px; right: 40px; font-size: 15px; }
  .letterhead .address { position: absolute; top: 62px; right: 40px; text-align: right; }
  .letter { position: absolute; top: 120px; left: 44px; width: 370px; }
  .letter .greeting { font-size: 12px; font-weight: 600; margin-bottom: 10px; }
  .letter p { font-size: 10px; line-height: 1.5; color: #666; margin-bottom: 9px; }
  .signature {
    width: 90px; height: 30px; margin-top: 16px;
    background: linear-gradient(90deg, rgba(58,58,58,.18), rgba(58,58,58,.05));
    border-radius: 12px;
  }
  .letterhead .contacts { position: absolute; left: 44px; bottom: 150px; }
  .letterhead .leaf-art { left: 170px; bottom: 70px; width: 260px; height: 200px; }

  /* Envelope front */
  .envelope-front { left: 610px; top: 110px; width: 560px; height: 244px; }
  .envelope-front .brand { position: absolute; top: 22px; left: 26px; font-size: 14px; }
  .envelope-front .address { position: absolute; top: 50px; left: 26px; }
  .envelope-front .contacts { position: absolute; top: 92px; left: 26px; font-size: 9.5px; line-height: 1.45; }
  .envelope-front .leaf-art { left: 220px; top: 50px; width: 260px; height: 170px; }

  /* Envelope back */
  .envelope-back { left: 610px; top: 420px; width: 560px; height: 244px; }
  .envelope-back .brand {
    position: absolute; top: 92px; left: 0; width: 100%;
    justify-content: center; color: var(--paper); font-size: 14px;
  }
  .envelope-back .brand-dot { background: var(--paper); }
  .envelope-back .address { position: absolute; bottom: 20px; right: 26px; text-align: right; }
</style>
</head>
<body>

<svg width="0" height="0" style="position:absolute">
  <defs>
    <symbol id="icon-phone" viewBox="0 0 10 10"><circle cx="5" cy="5" r="5" fill="#3bb54a"/><path d="M3.4 2.6l1 1-.5.6c.3.6.8 1.1 1.4 1.4l.6-.5 1 1-.6.8C4.8 6.8 3.2 5.2 2.6 3.2z" fill="#fff"/></symbol>
    <symbol id="icon-mail" viewBox="0 0 10 10"><circle cx="5" cy="5" r="5" fill="#3bb54a"/><rect x="2.6" y="3.3" width="4.8" height="3.4" fill="none" stroke="#fff" stroke-width=".7"/><path d="M2.6 3.3L5 5.2l2.4-1.9" fill="none" stroke="#fff" stroke-width=".7"/></symbol>
    <symbol id="icon-web" viewBox="0 0 10 10"><circle cx="5" cy="5" r="5" fill="#3bb54a"/><circle cx="5" cy="5" r="2.4" fill="none" stroke="#fff" stroke-width=".7"/><path d="M2.6 5h4.8M5 2.6v4.8" stroke="#fff" stroke-width=".6"/></symbol>
  </defs>
</svg>

<article class="sheet letterhead">
  <div class="brand"><span class="brand-dot"></span>Bright Harbor Dental</div>
  <address class="address" style="font-style:normal">
    <span class="name">Bright Harbor Dental</span><br>
    2215 Lantern Ridge Rd.<br>
    Suite 140 Lakewood, CO 80401
  </address>

  <section class="letter">
    <p class="greeting">Dear Mr. Carter.</p>
    <p>Thank you for choosing our practice for your family's dental care. We look forward to welcoming you at your next visit and keeping your smile healthy.</p>
    <p>Our team offers cleanings, exams, whitening and gentle restorative treatment in a calm and modern setting close to home.</p>
    <p>Please call our front desk with any questions about appointments, insurance or payment options. We are always happy to help.</p>
    <div class="signature" role="img" aria-label="Handwritten signature"></div>
  </section>

  <div class="leaf-art" role="img" aria-label="Faint leaf sprig illustration"></div>

  <ul class="contacts">
    <li><svg><use href="#icon-phone"/></svg>720-555-0142</li>
    <li><svg><use href="#icon-mail"/></svg>info@brightharbordental.com</li>
    <li><svg><use href="#icon-web"/></svg>www.brightharbordental.com</li>
  </ul>

  <svg class="wave" viewBox="0 0 470 150" height="150" preserveAspectRatio="none">
    <path d="M0 0 C140 70 300 110 470 95 L470 150 L0 150 Z" fill="var(--green-soft)" opacity=".7"/>
    <path d="M0 0 C140 70 300 110 470 95 L470 105 C300 120 140 85 0 14 Z" fill="var(--green)"/>
    <path d="M0 80 C160 120 320 140 470 128 L470 150 L0 150 Z" fill="var(--green)" opacity=".75"/>
  </svg>
</article>

<article class="sheet envelope-front">
  <div class="brand"><span class="brand-dot"></span>Bright Harbor Dental</div>
  <address class="address" style="font-style:normal">
    <span class="name">Bright Harbor Dental</span><br>
    2215 Lantern Ridge Rd.<br>
    Suite 140 Lakewood, CO 80401
  </address>
  <ul class="contacts">
    <li><svg><use href="#icon-phone"/></svg>720-555-0142</li>
    <li><svg><use href="#icon-mail"/></svg>info@brightharbordental.com</li>
    <li><svg><use href="#icon-web"/></svg>www.brightharbordental.com</li>
  </ul>
  <div class="leaf-art" role="img" aria-label="Faint leaf sprig illustration"></div>
  <svg class="wave" viewBox="0 0 560 110" height="110" preserveAspectRatio="none">
    <path d="M0 0 C170 40 360 75 560 70 L560 110 L0 110 Z" fill="var(--green-soft)" opacity=".7"/>
    <path d="M0 0 C170 40 360 75 560 70 L560 78 C360 86 170 55 0 12 Z" fill="var(--green)"/>
    <path d="M0 62 C180 90 380 104 560 96 L560 110 L0 110 Z" fill="var(--green)" opacity=".75"/>
  </svg>
</article>

<article class="sheet envelope-back">
  <svg style="position:absolute;left:0;top:0" width="560" height="180" viewBox="0 0 560 180">
    <path d="M0 0 H560 V40 C560 70 540 80 510 95 L300 170 C288 175 272 175 260 170 L20 80 C8 74 0 66 0 52 Z" fill="var(--green)"/>
  </svg>
  <div class="brand"><span class="brand-dot"></span>Bright Harbor Dental</div>
  <address class="address" style="font-style:normal">
    <span class="name">Bright Harbor Dental</span><br>
    2215 Lantern Ridge Rd.<br>
    Suite 140 Lakewood, CO 80401
  </address>
</article>

</body>
</html>
```